Larkspur Talent IT Recruiting firm needs a business card design for Recruiters, Sourcers, and Account

We need business cards that allow us to change all contact info, names, titles (Recruiter, Sourcer, Account Manager, Director, CEO, etc) per person since we have three offices, in three cities, Phoenix, Austin, and Las Vegas. We do recruiting and contractors for IT positions (Developers, Architects, Software Engineers, Security Engineers, Help Desk, DBAs, PMs, Scrum Masters, etc.) Our client companies are very diverse from Meridian 100 to silicone Valley type start-ups.

So, while we what hip, techie, and quirky, it still needs to be professional. Primary color we use is blue, with silver as a secondary color.

Target Market(s)

IT, Technology

Industry/Entity Type

Business

Contact Information for Business Card

Company name: Larkspur Talent, Inc.
Website: www.larkspurtalent.example
Logos for Careerloop, Blipster, and Myriada

Name, Title, Office Number, Cell Number, email

Font styles to use
Serif
Sans Serif

Colors
0455a3
d5d5d5

Requirements
Nice to have
• The grey I selected below is not necessary - but, would like silver included. I included a card design (File 3: LTI early trial example.jpg) that I had started on. It's very rough, and not quite what we're looking for, but what we did like is the logo, big, maybe a bit faded, off center, goes out of frame, etc. Still looking for other ideas - you are the pros! But, just an idea of a design element we liked.

```html
<!DOCTYPE html>
<html lang="en">
<head>
<meta charset="utf-8">
<title>Larkspur Talent — Business Card</title>
<link rel="stylesheet" href="https://fonts.googleapis.com/css2?family=Open+Sans:wght@400;600;700&family=Cormorant+SC:wght@500&display=swap">
<style>
  :root {
    --brand-blue: #0455a3;
    --silver: #d5d5d5;
    --silver-dark: #9c9c9c;
    --ink: #1a1a1a;
    --text-grey: #4a4a4a;
    --rule-grey: #9a9a9a;
    --paper: #ffffff;
    --backdrop: #eceef1;
  }
  * { margin: 0; padding: 0; box-sizing: border-box; }
  html, body {
    width: 1200px; height: 948px; overflow: hidden;
    background: var(--backdrop);
    font-family: "Open Sans", Arial, sans-serif;
  }
  .sheet {
    width: 1200px; height: 948px;
    display: flex; flex-direction: column; align-items: center; justify-content: center;
    gap: 56px;
  }
  .card {
    position: relative;
    width: 700px; height: 400px;
    overflow: hidden;
    box-shadow: 0 6px 18px rgba(0,0,0,0.18);
  }
  /* Front */
  .card-front { background: var(--paper); }
  .swoosh { position: absolute; left: 0; top: 0; width: 700px; height: 400px; }
  .brand {
    position: absolute; left: 52px; top: 98px;
    display: flex; align-items: center; gap: 14px;
  }
  .brand-dot {
    width: 30px; height: 30px; border-radius: 50%;
    background: var(--brand-blue); flex: none;
  }
  .brand-name {
    font-weight: 600; font-size: 40px; letter-spacing: 2px;
    color: var(--brand-blue); line-height: 1.05; text-transform: uppercase;
  }
  .tagline {
    position: absolute; left: 54px; top: 206px;
    font-family: "Cormorant SC", Georgia, serif;
    font-size: 17px; letter-spacing: 2px; color: var(--text-grey);
  }
  .divider {
    position: absolute; left: 420px; top: 52px;
    width: 1px; height: 220px; background: var(--rule-grey);
  }
  .contact { position: absolute; left: 440px; top: 60px; }
  .person-name { font-weight: 700; font-size: 19px; line-height: 26px; color: var(--brand-blue); }
  .person-title { font-size: 13px; line-height: 18px; color: var(--text-grey); margin-bottom: 12px; }
  .contact-list { list-style: none; }
  .contact-list li {
    display: flex; align-items: center; gap: 8px;
    font-size: 13px; color: var(--text-grey); line-height: 24px;
  }
  .contact-icon { width: 14px; height: 14px; flex: none; }
  /* Back */
  .card-back { background: var(--brand-blue); }
  .back-brand {
    position: absolute; left: 300px; top: 166px;
    display: flex; align-items: center; gap: 14px;
  }
  .back-brand .brand-dot { background: var(--paper); }
  .back-brand .brand-name { color: var(--paper); }
  .back-url {
    position: absolute; left: 40px; bottom: 30px;
    font-size: 16px; letter-spacing: 2px; color: var(--paper);
  }
</style>
</head>
<body>
<main class="sheet">
  <section class="card card-front" aria-label="Business card front">
    <svg class="swoosh" viewBox="0 0 700 400" aria-hidden="true">
      <path d="M0 318 C180 290 360 330 520 352 C600 362 660 360 700 350 L700 400 L0 400 Z" fill="var(--silver-dark)"/>
      <path d="M0 326 C180 298 360 338 520 360 C600 370 660 368 700 358 L700 400 L0 400 Z" fill="var(--ink)"/>
      <path d="M0 338 C180 312 360 350 520 372 C600 382 660 380 700 372 L700 400 L0 400 Z" fill="var(--brand-blue)"/>
    </svg>
    <div class="brand">
      <span class="brand-dot"></span>
      <span class="brand-name">Larkspur<br>Talent</span>
    </div>
    <p class="tagline">Talent That Moves Forward</p>
    <span class="divider"></span>
    <div class="contact">
      <p class="person-name">Maren Castillo</p>
      <p class="person-title">Client Relations Partner</p>
      <ul class="contact-list">
        <li>
          <svg class="contact-icon" viewBox="0 0 14 14" aria-hidden="true"><circle cx="7" cy="7" r="7" fill="var(--brand-blue)"/><path d="M4.5 3.5 L6 3.5 L6.6 5.4 L5.7 6.1 C6.2 7.2 6.9 7.9 8 8.4 L8.7 7.5 L10.5 8.1 L10.5 9.6 C7 9.8 4.3 7 4.5 3.5Z" fill="#fff"/></svg>
          555-010-4421
        </li>
        <li>
          <svg class="contact-icon" viewBox="0 0 14 14" aria-hidden="true"><circle cx="7" cy="7" r="7" fill="var(--brand-blue)"/><rect x="3.5" y="4.5" width="7" height="5" fill="none" stroke="#fff" stroke-width="1"/><path d="M3.5 4.5 L7 7.3 L10.5 4.5" fill="none" stroke="#fff" stroke-width="1"/></svg>
          maren@larkspurtalent.example
        </li>
        <li>
          <svg class="contact-icon" viewBox="0 0 14 14" aria-hidden="true"><circle cx="7" cy="7" r="7" fill="var(--brand-blue)"/><circle cx="7" cy="7" r="3.6" fill="none" stroke="#fff" stroke-width="1"/><path d="M3.4 7 H10.6" stroke="#fff" stroke-width="1"/></svg>
          www.larkspurtalent.example
        </li>
        <li>
          <svg class="contact-icon" viewBox="0 0 14 14" aria-hidden="true"><circle cx="7" cy="7" r="7" fill="var(--brand-blue)"/></svg>
          @MarenCastilloLT
        </li>
        <li>
          <svg class="contact-icon" viewBox="0 0 14 14" aria-hidden="true"><circle cx="7" cy="7" r="7" fill="var(--brand-blue)"/></svg>
          @MarenCastilloLT
        </li>
      </ul>
    </div>
  </section>

  <section class="card card-back" aria-label="Business card back">
    <div class="back-brand">
      <span class="brand-dot"></span>
      <span class="brand-name">Larkspur<br>Talent</span>
    </div>
    <p class="back-url">www.larkspurtalent.example</p>
  </section>
</main>
</body>
</html>
```